Verodex business card

Business card for sustainable investment company called "Verodex". Verodex is an exchange platform selling carbon credits between buyers and sellers. Carbon Credits are an environmental commodity for reducing global carbon emissions.

the card should obviously have our logo and the theme should be sustainability/environment mixed with a trading platform.

Contact Information for Business Card

Logo, Name, Title, Phone, Email

Colors
0054AA
0677BA
7BADD7
CADEEF
E8F1F8
0094D4
00A9DD
6FCCEA
C7EBF8
E9F6FB
00AB8E
00BBA5
67D7C9
C6EFE9
E9F9F6
59FF00
82FF00
B8FF75
E3FFCB
F4FFEA

```html
<!DOCTYPE html>
<html lang="en">
<head>
<meta charset="utf-8">
<title>Verodex business card</title>
<link href="https://fonts.googleapis.com/css2?family=Montserrat:wght@400;500;700&display=swap" rel="stylesheet">
<style>
  :root {
    --stage: #1c1c1d;
    --card: #0e0f11;
    --card-edge: #1c1f24;
    --white: #ffffff;
    --blue: #0094d4;
    --sky: #00a9dd;
    --sky-soft: #6fccea;
    --teal: #00bba5;
    --sea: #00ab8e;
    --leaf: #82ff00;
  }
  * { box-sizing: border-box; margin: 0; padding: 0; }
  html, body {
    width: 1200px; height: 900px; overflow: hidden;
    background: var(--stage);
    font-family: "Montserrat", sans-serif;
    color: var(--white);
  }
  .stage {
    position: relative; width: 1200px; height: 900px;
    display: flex; flex-direction: column; align-items: center; justify-content: center; gap: 44px;
  }
  .card {
    position: relative; width: 630px; height: 360px;
    background: linear-gradient(135deg, var(--card) 0%, var(--card) 55%, var(--card-edge) 100%);
    box-shadow: 0 18px 40px rgba(0,0,0,0.55);
    overflow: hidden;
  }
  .card__accent {
    position: absolute; left: 0; right: 0; bottom: 0; height: 4px;
    background: linear-gradient(90deg, var(--blue), var(--teal) 55%, var(--leaf));
  }
  .brand { position: relative; display: flex; align-items: center; gap: 18px; }
  .brand__square { width: 44px; height: 44px; background: var(--teal); }
  .brand__name {
    font-weight: 700; font-size: 54px; letter-spacing: 1px; text-transform: uppercase;
    color: var(--white); line-height: 1;
  }
  .card--front { display: flex; align-items: center; justify-content: center; }

  .backdrop-shape {
    position: absolute; right: -90px; top: 20px; width: 280px; height: 280px; border-radius: 50%;
    background: radial-gradient(circle at 35% 35%, rgba(0,187,165,0.16), rgba(0,148,212,0.10) 60%, rgba(0,148,212,0.04));
  }

  .card--back .brand { position: absolute; left: 56px; top: 52px; }
  .card--back .brand__square { width: 36px; height: 36px; }
  .card--back .brand__name { font-size: 44px; }

  .person { position: absolute; left: 40px; top: 148px; padding-left: 28px; }
  .person__bar { position: absolute; left: 0; top: 2px; width: 12px; height: 42px; background: var(--blue); }
  .person__name { font-weight: 700; font-size: 27px; color: var(--sky); letter-spacing: 1.5px; text-transform: uppercase; line-height: 1; }
  .person__title { font-weight: 400; font-size: 15px; letter-spacing: 1px; text-transform: uppercase; margin-top: 3px; }

  .contacts { position: absolute; left: 40px; top: 228px; list-style: none; }
  .contacts li { display: flex; align-items: center; gap: 12px; font-size: 16px; letter-spacing: 0.5px; height: 28px; }
  .contacts svg { width: 15px; height: 15px; flex: none; }
  .icon-fill { fill: var(--sky-soft); }
  .icon-line { fill: none; stroke: var(--sky-soft); stroke-width: 2; }

  .address {
    position: absolute; left: 330px; bottom: 36px; width: 270px;
    padding-left: 14px; border-left: 2px solid var(--teal);
    font-size: 14px; line-height: 1.4; letter-spacing: 0.4px;
  }
</style>
</head>
<body>
<main class="stage">
  <section class="card card--front">
    <div class="brand">
      <span class="brand__square"></span>
      <span class="brand__name">Verodex</span>
    </div>
    <span class="card__accent"></span>
  </section>

  <section class="card card--back">
    <span class="backdrop-shape" aria-hidden="true"></span>

    <div class="brand">
      <span class="brand__square"></span>
      <span class="brand__name">Verodex</span>
    </div>

    <div class="person">
      <span class="person__bar"></span>
      <p class="person__name">Dana Holt</p>
      <p class="person__title">Manager</p>
    </div>

    <ul class="contacts">
      <li>
        <svg viewBox="0 0 24 24" aria-hidden="true"><path class="icon-fill" d="M6.6 10.8a15.1 15.1 0 0 0 6.6 6.6l2.2-2.2a1 1 0 0 1 1-.25 11.4 11.4 0 0 0 3.6.57 1 1 0 0 1 1 1V20a1 1 0 0 1-1 1A17 17 0 0 1 3 4a1 1 0 0 1 1-1h3.5a1 1 0 0 1 1 1c0 1.25.2 2.45.57 3.6a1 1 0 0 1-.25 1z"/></svg>
        555-204-3187
      </li>
      <li>
        <svg viewBox="0 0 24 24" aria-hidden="true"><rect class="icon-line" x="3" y="6" width="18" height="13"/><path class="icon-line" d="M3 6l9 7 9-7"/></svg>
        hello@verodex-mail.com
      </li>
      <li>
        <svg viewBox="0 0 24 24" aria-hidden="true"><circle class="icon-line" cx="12" cy="12" r="9"/><ellipse class="icon-line" cx="12" cy="12" rx="4" ry="9"/><path class="icon-line" d="M3 12h18"/></svg>
        www.verodex-trade.com
      </li>
    </ul>

    <p class="address">2719 Birchwood Lane, Harbor Point Ave Fairhaven, OR 97411</p>
    <span class="card__accent"></span>
  </section>
</main>
</body>
</html>
```